Creation of a Velmaro website

Velmaro is a company% 26 # 233; t% 26 # 233; consulting that accompanies Swiss companies or% 26 # 233; strang% 26 # 232; res in the d% 26 # 233; development of their business on the market% 26 # 233; Switzerland by providing strategic contacts (personalized contact program% 26 # 233; s) or market information% 26 # 233; (% 26 # 233; market research% 26 # 233;) and by providing administrative support (repr% 26 # 233; tax representation) or logistics (organization of% 26 # 233; v% 26 # 233; nement, assistance for participation% 26 # 224; fairs). Our customers are mainly European companies wishing to develop their business in Switzerland. N% 26 # 233; however, our services are% 26 # 233; also aimed at Swiss companies wishing to develop in other parts of Switzerland. Our site must therefore be% 26 # 234; capable of being translated into several languages. The services offered% 26 # 233; s by Velmaro may also% 26 # 233; also% 26 # 39;% 26 # 233; tender% 26 # 224; promoting tourism in Switzerland for countries or regions% 26 # 233; foreigners or% 26 # 224; the promotion of trade fairs or fairs with% 26 # 232; sd% 26 # 39; companies of the sectors concerned% 26 # 233; s. It is therefore n% 26 # 233; necessary to be able to add sub-headings of services which can% 26 # 234; be displayed% 26 # 233; es or hide% 26 # 233; es as required. We are 2 associates% 26 # 233; s, low% 26 # 233; s in the French-speaking parts (Neuch% 26 # 226; tel) and al% 26 # 233; manique (Zurich) of Switzerland.

Target Market(s)

Swiss or European companies wishing to develop their activities in Switzerland.

Coding

Coded - Design and coding required

Colors

Designer to choose colors to be used in the design.

Requirements
Must have
• A home page A section of% 26 # 233; writing the services offered% 26 # 233; es by Velmaro with the possibility% 26 # 233; d% 26 # 39; add sub-headings which can% 26 # 234; be displayed% 26 # 233; e or hidden% 26 # 233; e A page with the r% 26 # 233; f% 26 # 233; which can be displayed% 26 # 233; e or hidden% 26 # 233; e A page of% 26 # 233; writing l% 26 # 39;% 26 # 233; team A page with form contact, addresses and int card% 26 # 233; gr% 26 # 233; e The site must% 26 # 234; be low% 26 # 233; on a CMS allowing% 26 # 39;% 26 # 234; to be autonomous in modifying the website The possibility% 26 # 233; to be able to translate the site into several languages (FR, EN, DE, IT, NL, ...)

```html
<!DOCTYPE html>
<html lang="en">
<head>
<meta charset="utf-8">
<title>Velmaro — Business Consulting</title>
<link href="https://fonts.googleapis.com/css2?family=Arimo:ital,wght@0,400;0,700;1,400&family=Archivo+Narrow:ital@1&family=Montserrat:wght@300&display=swap" rel="stylesheet">
<style>
:root{
  --navy:#1d3a55;
  --navy-dark:#17304a;
  --ink:#1a1a1a;
  --text:#555;
  --muted:#9a9a9a;
  --light:#f5f5f5;
  --grey:#e5e5e5;
  --white:#fff;
}
*{box-sizing:border-box;margin:0;padding:0}
html,body{width:1200px;height:3006px;overflow:hidden}
body{position:relative;font-family:"Arimo",Arial,sans-serif;color:var(--text);background:var(--white)}
.abs{position:absolute}
.brand{font-family:"Montserrat",sans-serif;font-weight:300;letter-spacing:2px;color:var(--white);display:flex;align-items:center;gap:10px}
.brand-mark{width:32px;height:32px;background:var(--white);border-radius:6px}
.btn{position:absolute;background:var(--navy);color:var(--white);border-radius:20px;font-size:14px;display:flex;align-items:center;justify-content:center}
.rule{position:absolute;height:3px;width:56px;background:var(--navy)}
.sec-title{position:absolute;left:0;width:1200px;text-align:center;font-size:27px;font-weight:700;color:var(--ink)}

/* top bar */
.topbar{top:0;left:0;width:1200px;height:42px;background:#050505;color:var(--white);font-size:13px}
/* hero */
.hero{top:42px;left:0;width:1200px;height:579px;background:linear-gradient(135deg,#2c2c2c,#4a4540 45%,#2a2622 75%,#1f1d1b)}
.hero-dim{top:0;left:0;width:1200px;height:621px;background:rgba(0,0,0,.25)}
.nav a{position:absolute;top:60px;color:var(--white);font-size:14px;text-decoration:none;transform:translateX(-50%)}
.hero h1{position:absolute;top:258px;left:0;width:1200px;text-align:center;color:var(--white);font-size:40px;font-weight:700}
.hero-copy{position:absolute;top:318px;left:240px;width:840px;text-align:center;color:var(--white);font-size:18px;line-height:23px}

/* welcome */
.welcome h2{position:absolute;top:688px;left:111px;font-size:27px;color:var(--ink)}
.welcome p{position:absolute;left:111px;width:461px;font-size:14px;line-height:16.5px;text-align:justify;color:#666}
.feature{position:absolute;width:250px}
.feature h3{position:absolute;left:61px;top:0;font-size:15px;font-weight:400;color:var(--ink);white-space:nowrap}
.feature p{position:absolute;left:61px;top:30px;width:130px;font-size:11px;line-height:13px;text-align:justify;color:#888}
.feature svg{position:absolute;left:0;top:30px}

/* what we do */
.wwd{top:1103px;left:0;width:1200px;height:682px;background:var(--light)}
.wwd-desc{position:absolute;top:1187px;left:170px;width:860px;text-align:center;font-size:13px;line-height:17px;color:#666}
.card{position:absolute;top:1266px;width:309px;height:437px;background:var(--white);box-shadow:0 0 4px rgba(0,0,0,.2)}
.card-img{height:190px;width:100%}
.card .cat{position:absolute;top:224px;left:31px;font-size:11px;color:var(--ink)}
.card h3{position:absolute;top:254px;left:31px;width:250px;font-size:19px;font-weight:400;line-height:22px;color:var(--ink)}
.card p{position:absolute;top:306px;left:31px;width:248px;font-size:11px;line-height:15.5px;text-align:justify;text-align-last:center;color:#777}
.dots{position:absolute;display:flex;gap:8px;align-items:center;transform:translateX(-50%)}
.dots i{display:block;width:6px;height:6px;border-radius:50%;background:var(--navy)}
.dots i.on{width:13px;height:13px;border:3px solid var(--navy);background:transparent}

/* clients */
.clients{top:1785px;left:0;width:1200px;height:342px;background:var(--grey)}
.arrow{position:absolute;top:1928px;width:44px;height:44px;border-radius:50%;background:var(--white);display:flex;align-items:center;justify-content:center}
.client{position:absolute;top:1938px;transform:translateX(-50%);display:flex;align-items:center;gap:8px;font-size:22px;font-weight:700;color:#6b6b6b}
.client i{display:block;width:14px;height:14px;border:2px solid #6b6b6b}

/* testimonials */
.quote{position:absolute;top:2250px;width:314px;height:154px;background:var(--white);border:1px solid #ddd;border-radius:10px;box-shadow:0 2px 6px rgba(0,0,0,.12)}
.quote p{padding:32px 34px 0;font-family:"Archivo Narrow",sans-serif;font-style:italic;font-size:11.5px;line-height:19.5px;text-align:center;color:#444}
.quote .tip{position:absolute;left:50%;bottom:-13px;width:22px;height:22px;margin-left:-11px;background:var(--white);border-right:1px solid #ddd;border-bottom:1px solid #ddd;transform:rotate(45deg)}
.person{position:absolute;top:2433px;width:314px;text-align:center}
.avatar{width:62px;height:62px;border-radius:50%;margin:0 auto;background:linear-gradient(160deg,#c9b8a6,#6f5a48)}
.person .name{margin-top:10px;font-size:19px;color:var(--navy)}
.person .role{margin-top:4px;font-size:13px;color:#aaa}
.tdots{position:absolute;top:2572px;left:560px;display:flex;gap:22px;align-items:center}
.tdots i{display:block;width:9px;height:9px;border-radius:50%;background:#ccc}
.tdots i.on{width:14px;height:14px;background:var(--navy)}

/* footer */
.footer{top:2639px;left:0;width:1200px;height:367px;background:var(--navy)}
.footer-text{position:absolute;top:2712px;left:109px;width:280px;font-size:14px;line-height:21.5px;text-align:justify;text-align-last:center;color:#d5dde5}
.footer h4{position:absolute;font-size:17px;color:var(--white)}
.flink{position:absolute;font-size:13px;color:#c7d1dc}
.hlink{position:absolute;font-size:16px;color:#c7d1dc}
.social{position:absolute;top:2896px;display:flex;gap:8px}
.social span{display:flex;align-items:center;gap:4px;font-size:12px;color:var(--white)}
.social i{display:block;width:22px;height:22px;background:var(--white)}
.foot-rule{position:absolute;top:2958px;left:0;width:1200px;height:1px;background:#3d5a76}
.copy{position:absolute;top:2970px;left:0;width:1185px;text-align:center;font-size:13px;color:#c7d1dc}
</style>
</head>
<body>

<!-- top bar -->
<div class="abs topbar">
  <svg class="abs" style="left:167px;top:14px" width="20" height="14" viewBox="0 0 20 14"><rect x="1" y="1" width="18" height="12" fill="none" stroke="#fff" stroke-width="1.3"/><path d="M1 1l9 7 9-7" fill="none" stroke="#fff" stroke-width="1.3"/></svg>
  <span class="abs" style="left:197px;top:13px">hello@velmaro-consult.com</span>
  <span class="abs" style="left:400px;top:9px;width:1px;height:24px;background:#fff"></span>
  <svg class="abs" style="left:444px;top:14px" width="14" height="14" viewBox="0 0 24 24"><path fill="#fff" d="M6.6 10.8a15 15 0 006.6 6.6l2.2-2.2a1 1 0 011-.25 11.4 11.4 0 003.6.57 1 1 0 011 1V20a1 1 0 01-1 1A17 17 0 013 4a1 1 0 011-1h3.5a1 1 0 011 1c0 1.25.2 2.45.57 3.6a1 1 0 01-.25 1z"/></svg>
  <span class="abs" style="left:465px;top:13px">+41 32 555 0148</span>
  <span class="abs" style="left:998px;top:13px">En</span>
  <span class="abs" role="img" aria-label="Language flag" style="left:1029px;top:13px;width:28px;height:16px;background:linear-gradient(#c8102e,#fff 50%,#012169)"></span>
  <svg class="abs" style="left:1063px;top:16px" width="10" height="7" viewBox="0 0 10 7"><path d="M1 1l4 4 4-4" fill="none" stroke="#fff" stroke-width="1.8"/></svg>
</div>

<!-- hero -->
<div class="abs hero" role="img" aria-label="Photo of colleagues discussing documents in a meeting"></div>
<div class="abs hero-dim"></div>
<div class="abs brand" style="top:52px;left:111px;font-size:26px"><span class="brand-mark"></span>VELMARO</div>
<span class="abs" style="left:418px;top:52px;width:16px;height:2px;background:#fff"></span>
<nav class="nav">
  <a style="left:425px">HOME</a>
  <a style="left:525px">ABOUT US</a>
  <a style="left:640px">SERVICES</a>
  <a style="left:761px">PORTFOLIO</a>
  <a style="left:866px">BLOG</a>
</nav>
<div class="btn" style="top:49px;left:942px;width:146px;height:38px">CONTACT US</div>
<section class="hero-content">
  <h1 class="hero">SUCCESS DEFINED IN A DIFFERENT WAY</h1>
  <p class="hero-copy">Lorem Ipsum is simply dummy text of the printing and typesetting industry. Lorem Ipsum has been the industry's standard dummy text ever since the 1500s, when an unknown printer took a galley of type and scrambled it to make a type</p>
</section>
<div class="btn" style="top:404px;left:552px;width:148px;height:38px;font-size:13px">Read More</div>

<!-- welcome -->
<section class="welcome">
  <span class="rule" style="top:677px;left:111px"></span>
  <h2>WELCOME TO VELMARO</h2>
  <p style="top:734px">Lorem Ipsum is simply dummy text of the printing and typesetting industry. Lorem Ipsum has been the industry's standard dummy text ever since the 1500s, when an unknown printer took a galley of type and scrambled it to make a type</p>
  <p style="top:817px">Sed ut perspiciatis unde omnis iste natus error sit voluptatem accusantium doloremque laudantium, totam rem aperiam, eaque ipsa quae ab illo inventore veritatis et quasi architecto beatae vitae dicta sunt explicabo. Nemo enim ipsam voluptatem quia voluptas sit aspernatur aut odit aut fugit, sed quia consequuntur magni dolores eos qui ratione voluptatem sequi nesciunt. Neque porro quisquam est, qui dolorem ipsum quia dolor sit amet, consectetur, adipisci velit, sed quia non numquam eius modi tempora incidunt ut labore et dolore magnam aliquam quaerat voluptatem. Ut enim ad minima veniam, quis nostrum.</p>
  <div class="btn" style="top:1023px;left:109px;width:148px;height:39px;font-size:13px">Read More</div>

  <div class="feature" style="top:716px;left:607px">
    <svg width="56" height="50" viewBox="0 0 56 50"><g fill="none" stroke="#1d3a55" stroke-width="2.4"><rect x="3" y="12" width="50" height="34" rx="2"/><path d="M20 12V5h16v7M3 24h50M24 21h8v7h-8z"/></g></svg>
    <h3>Job Consulting</h3>
    <p>Lorem Ipsum is simply dummy text of the printing and typesetting industry. Lorem Ipsum has been the industry's standard dummy text ever since the 1500s,</p>
  </div>
  <div class="feature" style="top:716px;left:864px">
    <svg width="56" height="58" viewBox="0 0 56 58"><g fill="none" stroke="#1d3a55" stroke-width="2.4"><path d="M28 10a14 14 0 00-8 25.5V42h16v-6.5A14 14 0 0028 10zM21 47h14M23 52h10"/><path d="M2 12l6 5M54 12l-6 5M28 1v5M2 32h5M49 32h5"/></g></svg>
    <h3>Business Tips</h3>
    <p>Lorem Ipsum is simply dummy text of the printing and typesetting industry. Lorem Ipsum has been the industry's standard dummy text ever since the 1500s,</p>
  </div>
  <div class="feature" style="top:870px;left:607px">
    <svg width="64" height="58" viewBox="0 0 64 58"><g fill="none" stroke="#1d3a55" stroke-width="2.4"><path d="M4 28l32-20 8 28-36 2zM10 38l6 16h7l-3-14M44 10l4 30"/><path d="M52 14l8-5M54 24h8M52 33l7 4"/></g></svg>
    <h3>Marketing Analysis</h3>
    <p>Lorem Ipsum is simply dummy text of the printing and typesetting industry. Lorem Ipsum has been the industry's standard dummy text ever since the 1500s,</p>
  </div>
  <div class="feature" style="top:870px;left:864px">
    <svg width="60" height="60" viewBox="0 0 60 60"><g fill="none" stroke="#1d3a55" stroke-width="2.4"><path d="M56 4C40 4 26 14 18 30l12 12C46 34 56 20 56 4z"/><circle cx="40" cy="20" r="5"/><path d="M18 30l-10-2 8-10h10M30 42l2 10 10-8V34M14 40l-8 14 14-8M10 46l-4 4"/></g></svg>
    <h3>Business Solutions</h3>
    <p>Lorem Ipsum is simply dummy text of the printing and typesetting industry. Lorem Ipsum has been the industry's standard dummy text ever since the 1500s,</p>
  </div>
</section>

<!-- what we do -->
<section>
  <div class="abs wwd"></div>
  <span class="rule" style="top:1127px;left:572px"></span>
  <h2 class="sec-title" style="top:1141px">WHAT WE DO</h2>
  <p class="wwd-desc">Lorem Ipsum is simply dummy text of the printing and typesetting industry. Lorem Ipsum has been the industry's standard dummy text ever since the 1500s, when an unknown printer took a galley of type and scrambled it to make a type</p>
  <article class="card" style="left:112px">
    <div class="card-img" role="img" aria-label="Photo of business team standing in an office" style="background:linear-gradient(135deg,#d8d8d8,#7a7a7a 60%,#bdbdbd)"></div>
    <span class="cat">Capital, Economy</span>
    <h3>We Help Your Time Work For Your Money.</h3>
    <p>Lorem Ipsum is simply dummy text of the printing and typesetting industry. Lorem Ipsum has been the industry's standard dummy text ever since the 1500s, when an unknown printer took a galley of type and scrambled it to make a type</p>
  </article>
  <article class="card" style="left:448px">
    <div class="card-img" role="img" aria-label="Photo of colleagues working around a meeting table" style="background:linear-gradient(135deg,#5a5048,#9a8f86 50%,#3c4656)"></div>
    <span class="cat">Capital, Economy</span>
    <h3>You Have Roots Here Now, Grow With Us.</h3>
    <p>Lorem Ipsum is simply dummy text of the printing and typesetting industry. Lorem Ipsum has been the industry's standard dummy text ever since the 1500s, when an unknown printer took a galley of type and scrambled it to make a type</p>
  </article>
  <article class="card" style="left:780px">
    <div class="card-img" role="img" aria-label="Photo of a business meeting in a bright office" style="background:linear-gradient(135deg,#e6e6e6,#8c8c8c 55%,#cfcfcf)"></div>
    <span class="cat">Capital, Economy</span>
    <h3>Experience And Resources By Your Side.</h3>
    <p>Lorem Ipsum is simply dummy text of the printing and typesetting industry. Lorem Ipsum has been the industry's standard dummy text ever since the 1500s, when an unknown printer took a galley of type and scrambled it to make a type</p>
  </article>
  <div class="dots" style="top:1744px;left:600px"><i></i><i class="on"></i><i></i></div>
</section>

<!-- clients -->
<section>
  <div class="abs clients"></div>
  <span class="rule" style="top:1830px;left:572px"></span>
  <h2 class="sec-title" style="top:1845px">OUR CLIENTS</h2>
  <div class="arrow" style="left:56px"><svg width="20" height="16" viewBox="0 0 20 16"><path d="M19 8H3M9 2L3 8l6 6" fill="none" stroke="#1d3a55" stroke-width="2.6"/></svg></div>
  <div class="arrow" style="left:1095px"><svg width="20" height="16" viewBox="0 0 20 16"><path d="M1 8h16M11 2l6 6-6 6" fill="none" stroke="#1d3a55" stroke-width="2.6"/></svg></div>
  <div class="client" style="left:205px"><i></i>Tervan</div>
  <div class="client" style="left:363px">Olmora</div>
  <div class="client" style="left:518px">Casku</div>
  <div class="client" style="left:677px">Zendro</div>
  <div class="client" style="left:834px"><i></i>Arenox</div>
  <div class="client" style="left:992px">Brisko</div>
  <div class="dots" style="top:2057px;left:600px"><i></i><i class="on" style="background:var(--navy);border:0;width:12px;height:12px"></i><i></i></div>
</section>

<!-- happy customers -->
<section>
  <span class="rule" style="top:2162px;left:572px"></span>
  <h2 class="sec-title" style="top:2180px;color:var(--navy)">HAPPY CUSTOMERS</h2>
  <div class="quote" style="left:112px"><p>Lorem ipsum dolor sit amet, consectetur adipiscing elit, sed do eiusmod tempor incididunt ut labore et dolore magna aliqua. Quis ipsum suspendisse ultrices gravida. Risus commodo viverra maecenas accumsan lacus vel facilisis.</p><span class="tip"></span></div>
  <div class="quote" style="left:446px"><p>Lorem ipsum dolor sit amet, consectetur adipiscing elit, sed do eiusmod tempor incididunt ut labore et dolore magna aliqua. Quis ipsum suspendisse ultrices gravida. Risus commodo viverra maecenas accumsan lacus vel facilisis.</p><span class="tip"></span></div>
  <div class="quote" style="left:774px"><p>Lorem ipsum dolor sit amet, consectetur adipiscing elit, sed do eiusmod tempor incididunt ut labore et dolore magna aliqua. Quis ipsum suspendisse ultrices gravida. Risus commodo viverra maecenas accumsan lacus vel facilisis.</p><span class="tip"></span></div>
  <div class="person" style="left:112px"><div class="avatar" role="img" aria-label="Customer portrait"></div><div class="name">Lukas Ammann</div><div class="role">Software Engineer, Nordal</div></div>
  <div class="person" style="left:446px"><div class="avatar" role="img" aria-label="Customer portrait" style="background:linear-gradient(160deg,#8aa6c8,#3a3a3a)"></div><div class="name">Marc Delacour</div><div class="role">Software Engineer, Nordal</div></div>
  <div class="person" style="left:774px"><div class="avatar" role="img" aria-label="Customer portrait" style="background:linear-gradient(160deg,#e9e4de,#7d6452)"></div><div class="name">Silvio Renz</div><div class="role">Software Engineer, Nordal</div></div>
  <div class="tdots"><i></i><i class="on"></i><i></i><i></i></div>
</section>

<!-- footer -->
<footer>
  <div class="abs footer"></div>
  <div class="abs brand" style="top:2660px;left:111px;font-size:22px"><span class="brand-mark" style="width:26px;height:26px;border-radius:5px"></span>VELMARO</div>
  <p class="footer-text">Lorem Ipsum is simply dummy text of the printing and typesetting industry. Lorem Ipsum has been the industry's standard dummy text ever since the 1500s, when an unknown printer took a galley of type and scrambled it to make a type</p>
  <p class="abs" style="top:2864px;left:111px;font-size:14px;line-height:16px;color:#d5dde5">14 Rue du Lac, 2000 Neuchâtel,<br>Switzerland.</p>
  <p class="abs" style="top:2926px;left:111px;font-size:14px;color:#d5dde5">032-555-0192</p>

  <h4 style="top:2666px;left:575px">INFORMATION</h4>
  <span class="flink" style="top:2718px;left:577px">HOME</span>
  <span class="flink" style="top:2756px;left:577px">ABOUT US</span>
  <span class="flink" style="top:2794px;left:577px">SERVICES</span>
  <span class="flink" style="top:2831px;left:577px">PORTFOLIO</span>
  <span class="flink" style="top:2869px;left:577px">BLOG</span>
  <span class="flink" style="top:2907px;left:577px">CONTACTUS</span>

  <h4 style="top:2666px;left:858px">HELP &amp; SUPPORT</h4>
  <span class="hlink" style="top:2716px;left:858px">Contacts</span>
  <span class="hlink" style="top:2754px;left:858px">My Account</span>
  <span class="hlink" style="top:2791px;left:858px">Cart</span>
  <span class="abs" style="top:2862px;left:858px;font-size:15px;font-weight:700;color:#fff">Follow Us:</span>
  <div class="social" style="left:858px"><span><i></i>Linkup</span><span><i></i>Facepage</span><span><i></i>Chirpr</span></div>

  <span class="foot-rule"></span>
  <p class="copy">Copyright © 2006-2020 Velmaro</p>
</footer>

</body>
</html>
```